BUSINESS CARD DESIGN

NAME- DALE VORSKIN
PHONE NUMER - 555- 714-9082
EMAIL- OFFICE@TRV-GROUNDMAKRZ.COM
BACK OF CARD- SPEACIALIZES IN LAND CLEARING, FORESTRY MUCLHING AND EXCAVATION

Contact Information for Business Card

NAME- DALE VORSKIN PHONE NUMER - 555- 714-9082 EMAIL- OFFICE@TRV-GROUNDMAKRZ.COM BACK OF CARD- SPEACIALIZES IN LAND CLEARING , MUCLHING AND EXCAVATION

```html
<!DOCTYPE html>
<html lang="en">
<head>
<meta charset="utf-8">
<title>Traverse Groundmakrz – Business Card</title>
<link rel="stylesheet" href="https://fonts.googleapis.com/css2?family=Roboto+Condensed:wght@300;400;700&display=swap">
<style>
  :root {
    --backdrop: #e4e8e9;
    --card: #212226;
    --accent: #f7b523;
    --ink-light: #f2f2f2;
    --emboss: #1a1b1e;
    --emboss-ink: #2a2b2f;
  }
  * { box-sizing: border-box; margin: 0; padding: 0; }
  html, body { width: 1200px; height: 960px; overflow: hidden; }
  body {
    background: var(--backdrop);
    font-family: "Roboto Condensed", Arial, sans-serif;
    position: relative;
  }
  .card {
    position: absolute;
    left: 252px;
    width: 700px;
    height: 400px;
    border-radius: 34px;
    background: var(--accent);
  }
  .card-face {
    position: absolute;
    left: 4px; top: 0; right: 0; bottom: 4px;
    border-radius: 32px;
    background: var(--card);
    overflow: hidden;
  }
  .card--front { top: 60px; }
  .card--back { top: 500px; }

  /* front */
  .brand-mark {
    position: absolute;
    left: 50%; top: 82px;
    width: 130px; height: 130px;
    margin-left: -67px;
    border-radius: 50%;
    border: 5px solid var(--accent);
  }
  .brand-lockup {
    position: absolute;
    left: 0; right: 0;
    text-align: center;
    color: var(--accent);
    font-weight: 700;
    text-transform: uppercase;
  }
  .card--front .brand-lockup { top: 238px; }
  .brand-name { font-size: 24px; letter-spacing: 1px; line-height: 1.1; }
  .brand-sub { font-size: 14px; letter-spacing: 6px; line-height: 1.5; }
  .brand-phone { font-size: 13px; letter-spacing: 9px; line-height: 1.5; }
  .tagline {
    position: absolute;
    left: 0; right: 0; top: 356px;
    text-align: center;
    color: var(--accent);
    font-size: 16px;
    letter-spacing: 0.3px;
  }

  /* back */
  .back-mark {
    position: absolute;
    left: 10px; top: 44px;
    width: 330px; height: 300px;
    border-radius: 50%;
    background: var(--emboss);
    display: flex; align-items: center; justify-content: center;
    color: var(--emboss-ink);
    font-weight: 700;
    font-size: 26px;
    text-align: center;
    line-height: 1.15;
  }
  .card--back .brand-lockup {
    left: 378px; right: 30px; top: 30px;
  }
  .card--back .brand-name { font-size: 22px; }
  .person-name {
    position: absolute;
    right: 24px; top: 215px;
    color: var(--accent);
    font-size: 42px;
    letter-spacing: 0.5px;
    white-space: nowrap;
  }
  .person-name .first { font-weight: 700; }
  .person-name .last { font-weight: 300; }
  .contact-list {
    position: absolute;
    right: 24px; top: 296px;
    list-style: none;
  }
  .contact-item {
    display: flex; align-items: center; justify-content: flex-end;
    gap: 8px;
    height: 23px;
    color: var(--ink-light);
    font-size: 16px;
    letter-spacing: 0.4px;
  }
  .contact-icon { width: 16px; height: 16px; flex: none; }
</style>
</head>
<body>

<section class="card card--front" aria-label="Card front">
  <div class="card-face">
    <div class="brand-mark"></div>
    <div class="brand-lockup">
      <div class="brand-name">Traverse Groundmakrz</div>
      <div class="brand-sub">LLC · Hawaii</div>
      <div class="brand-phone">555-714-9082</div>
    </div>
    <p class="tagline">SPEACIALIZES IN LAND CLEARING , MUCLHING AND EXCAVATION</p>
  </div>
</section>

<section class="card card--back" aria-label="Card back">
  <div class="card-face">
    <div class="back-mark">TRAVERSE<br>GROUNDMAKRZ</div>
    <div class="brand-lockup">
      <div class="brand-name">Traverse Groundmakrz</div>
      <div class="brand-sub">LLC · Hawaii</div>
      <div class="brand-phone">555-714-9082</div>
    </div>
    <h1 class="person-name"><span class="first">DALE</span> <span class="last">VORSKIN</span></h1>
    <ul class="contact-list">
      <li class="contact-item">555- 714-9082
        <svg class="contact-icon" viewBox="0 0 24 24" aria-hidden="true"><path fill="#f7b523" d="M6.6 10.8a15 15 0 0 0 6.6 6.6l2.2-2.2c.3-.3.7-.4 1-.2 1.1.4 2.3.6 3.6.6.6 0 1 .4 1 1V20c0 .6-.4 1-1 1A17 17 0 0 1 3 4c0-.6.4-1 1-1h3.5c.6 0 1 .4 1 1 0 1.3.2 2.5.6 3.6.1.3 0 .7-.2 1z"/></svg>
      </li>
      <li class="contact-item">WWW.TRV-GROUNDMAKRZ.COM
        <svg class="contact-icon" viewBox="0 0 24 24" aria-hidden="true"><circle cx="12" cy="12" r="9.5" fill="none" stroke="#f7b523" stroke-width="2"/><path d="M2.5 12h19M12 2.5c3 3 3 16 0 19M12 2.5c-3 3-3 16 0 19" fill="none" stroke="#f7b523" stroke-width="1.6"/></svg>
      </li>
      <li class="contact-item">OFFICE@TRV-GROUNDMAKRZ.COM
        <svg class="contact-icon" viewBox="0 0 24 24" aria-hidden="true"><rect x="2" y="5" width="20" height="15" rx="1.5" fill="#f7b523"/><path d="M2.5 6l9.5 7 9.5-7" fill="none" stroke="#212226" stroke-width="1.8"/></svg>
      </li>
    </ul>
  </div>
</section>

</body>
</html>
```